Fenwick Grading LTD - website for irrigation & Landscape Lighting & Buried service wire

Looking for a website to help promote my business with Irrigation (installation, service, etc) and buried service wire/drainage solutions.

Commercial/Residential

Landscape lighting.

I’ll get photos in the trucks and trailers to upload as well maybe the machine as well.

Target Market(s)

Homeowners who want green grass and beautiful gardens. Beautiful landscape lighting

Industry/Entity Type

Irrigation systems and landscape lighting and buried service wire to homes and offering Drainage soltions.

Coding

Coded - Design and coding required

Number of Pages Required

4 page

Colors
F0912C
F2A743
F7CA91
FBE8D2
FDF5EE

Requirements
Must have
• was hoping to link up my email on fenwickgrading@mailbox-example.net with the website if possible.
Nice to have
• Page for Irrigation, page for landscape lighting, page buried service wire & drainage soltions.

```html
<!DOCTYPE html>
<html lang="en">
<head>
<meta charset="utf-8">
<title>Contact Us – Fenwick Grading LTD</title>
<link href="https://fonts.googleapis.com/css2?family=Montserrat:wght@400;500;600&family=Roboto+Condensed:wght@700&display=swap" rel="stylesheet">
<style>
:root{
  --orange:#F0912C;
  --orange-2:#F2A743;
  --peach:#F7CA91;
  --cream:#FBE8D2;
  --ivory:#FDF5EE;
  --ink:#111;
  --text:#222;
  --muted:#9a9a9a;
  --line:#dcdcdc;
  --white:#fff;
}
*{box-sizing:border-box;margin:0;padding:0}
html,body{width:1200px;height:2381px;overflow:hidden;background:var(--white)}
body{position:relative;font-family:'Montserrat',sans-serif;color:var(--text)}
.abs{position:absolute}
.hero{left:0;top:0;width:1200px;height:440px}
.brand{left:141px;top:22px;color:var(--orange);font-weight:600;font-size:22px;line-height:1.15;width:170px}
.brand small{display:block;font-size:22px;color:var(--orange)}
.nav{top:34px;display:flex;font-size:13px;color:var(--white);font-weight:500}
.nav a{color:inherit;text-decoration:none}
.cta{left:939px;top:25px;width:120px;height:35px;border-radius:18px;background:var(--orange);color:var(--white);font-size:11.5px;font-weight:600;letter-spacing:.5px;display:flex;align-items:center;justify-content:center}
.page-title{left:141px;top:186px;font-family:'Roboto Condensed',sans-serif;font-size:37px;color:var(--white)}
.crumbs{left:141px;top:232px;font-size:13px;color:var(--white)}
.crumbs b{font-weight:600}
.section-title{left:0;width:1200px;text-align:center;font-family:'Roboto Condensed',sans-serif;font-size:37px;color:var(--ink)}
.section-title span{color:var(--orange)}
.intro{left:170px;width:860px;top:587px;text-align:center;font-size:13.5px;line-height:23px;color:var(--ink)}
.info{top:680px;width:260px;text-align:center}
.info .dot{width:50px;height:50px;border-radius:50%;background:var(--orange);margin:0 auto;display:flex;align-items:center;justify-content:center}
.info h3{font-size:16px;font-weight:600;margin-top:17px;color:var(--ink)}
.info p{font-size:13px;line-height:21px;margin-top:14px;color:#333}
.map{left:141px;top:903px;width:918px;height:494px;border-radius:28px;background:linear-gradient(135deg,#f5f1e8,#eef0e3 45%,#e6efe0 70%,#f3efe6);overflow:hidden}
.pin-card{left:591px;top:182px;width:235px;height:66px;background:var(--white);border-radius:6px;box-shadow:0 2px 8px rgba(0,0,0,.15);padding:10px 15px;font-size:11.5px;line-height:16px;color:#333}
.pin-card b{font-weight:500;color:var(--ink)}
.field{border:1.5px solid var(--line);border-radius:6px;background:var(--white);font-size:13px;color:var(--muted);padding:17px 27px}
.send{left:545px;top:1832px;width:110px;height:40px;border-radius:20px;background:var(--orange);color:var(--white);font-size:12px;font-weight:600;letter-spacing:1px;display:flex;align-items:center;justify-content:center}
.footer{left:0;top:1950px;width:1200px;height:431px}
.foot-brand{left:0;width:1200px;top:2080px;text-align:center;color:var(--orange);font-weight:600;font-size:34px;line-height:1.1}
.foot-nav{top:2194px;left:0;width:1200px;display:flex;justify-content:center;gap:0;font-size:13.5px;color:var(--white)}
.foot-nav span{margin:0 27px}
.foot-info{top:2252px;display:flex;align-items:center;color:var(--white);font-size:13.5px;line-height:21px}
.ring{width:36px;height:36px;border:1.5px solid var(--orange);border-radius:50%;display:flex;align-items:center;justify-content:center;margin-right:9px}
.divider{left:141px;top:2317px;width:918px;height:1px;background:#333}
.copy{left:141px;top:2340px;color:var(--white);font-size:13px}
.social{top:2332px;width:33px;height:33px;border:1.5px solid var(--orange);border-radius:50%}
</style>
</head>
<body>

<svg class="abs hero" viewBox="0 0 1200 440" role="img" aria-label="Photograph of a landscaped garden with curved stone edging and lit garden lights at dusk">
  <defs>
    <linearGradient id="heroFill" x1="0" y1="0" x2="1" y2="1">
      <stop offset="0" stop-color="#3c4a22"/>
      <stop offset=".45" stop-color="#5c6a2c"/>
      <stop offset=".75" stop-color="#6e6a34"/>
      <stop offset="1" stop-color="#2f3a20"/>
    </linearGradient>
  </defs>
  <polygon points="0,0 1200,0 1200,355 600,428 0,363" fill="var(--orange)"/>
  <polygon points="0,0 1200,0 1200,348 600,416 0,356" fill="url(#heroFill)"/>
  <rect width="1200" height="140" fill="rgba(0,0,0,.25)"/>
</svg>

<div class="abs brand">Fenwick Grading <small>LTD</small></div>
<nav class="abs nav" style="left:408px"><a style="margin-right:45px">Home</a><a style="margin-right:45px">Irrigation</a><a style="margin-right:45px">Landscape Lighting</a><a>Trenching&nbsp; Services</a></nav>
<div class="abs cta">CONTACT US</div>
<h1 class="abs page-title">Contact Us</h1>
<div class="abs crumbs">Home » <b>Contact Us</b></div>

<h2 class="abs section-title" style="top:520px">Get In <span>Touch</span></h2>
<p class="abs intro">Lorem Ipsum is simply dummy text of the printing and typesetting industry. Lorem Ipsum has been the industry's standard dummy text ever since the 1500s, when an unknown printer took a galley of type and scrambled it to make a type specimen book.</p>

<div class="abs info" style="left:180px">
  <div class="dot"><svg width="22" height="22" viewBox="0 0 24 24"><path fill="#fff" d="M6.6 10.8a15 15 0 006.6 6.6l2.2-2.2c.3-.3.7-.4 1-.2 1.1.4 2.3.6 3.6.6.6 0 1 .4 1 1V20c0 .6-.4 1-1 1A17 17 0 013 4c0-.6.4-1 1-1h3.5c.6 0 1 .4 1 1 0 1.3.2 2.5.6 3.6.1.3 0 .7-.2 1z"/></svg></div>
  <h3>Phone</h3><p>+123 456 7890</p>
</div>
<div class="abs info" style="left:470px">
  <div class="dot"><svg width="20" height="24" viewBox="0 0 20 24"><path fill="#fff" d="M10 0a8 8 0 018 8c0 6-8 16-8 16S2 14 2 8a8 8 0 018-8zm0 5a3 3 0 100 6 3 3 0 000-6z"/></svg></div>
  <h3>Address</h3><p>123, Building Name, Street<br>City, State XY 123456</p>
</div>
<div class="abs info" style="left:758px">
  <div class="dot"><svg width="24" height="18" viewBox="0 0 24 18"><rect x="1" y="1" width="22" height="16" rx="2" fill="#fff"/><path d="M2 3l10 7 10-7" stroke="var(--orange)" stroke-width="2" fill="none"/></svg></div>
  <h3>Email Us</h3><p>info@fenwickgrading-example.net</p>
</div>

<div class="abs map" role="img" aria-label="Map showing the business location">
  <svg class="abs" style="left:540px;top:200px" width="28" height="36" viewBox="0 0 20 26"><path fill="var(--orange)" d="M10 0a9 9 0 019 9c0 7-9 17-9 17S1 16 1 9a9 9 0 019-9z"/><circle cx="10" cy="9" r="3.5" fill="#fff"/></svg>
  <div class="abs pin-card"><b>Fenwick Grading Irrigation Systems</b><br>123, Building Name, Street<br>City, State XY 123456</div>
</div>

<h2 class="abs section-title" style="top:1473px">Send A <span>Message</span></h2>
<div class="abs field" style="left:276px;top:1551px;width:317px;height:50px">First Name*</div>
<div class="abs field" style="left:607px;top:1551px;width:317px;height:50px">Last Name*</div>
<div class="abs field" style="left:276px;top:1623px;width:317px;height:50px">Email Address*</div>
<div class="abs field" style="left:607px;top:1623px;width:317px;height:50px">Phone Number*</div>
<div class="abs field" style="left:276px;top:1695px;width:648px;height:94px;padding-top:14px">Message*</div>
<div class="abs send">SEND</div>

<svg class="abs footer" viewBox="0 0 1200 431" aria-hidden="true">
  <polygon points="0,80 600,6 1200,88 1200,431 0,431" fill="var(--orange)"/>
  <polygon points="0,82 600,18 1200,90 1200,431 0,431" fill="#000"/>
</svg>
<div class="abs foot-brand">Fenwick Grading<br>LTD</div>
<div class="abs foot-nav"><span>Home</span><span>Irrigation</span><span>Landscape Lighting</span><span>Trenching&nbsp; Services</span><span style="font-weight:600;font-size:12.5px">Contact Us</span></div>

<div class="abs foot-info" style="left:207px">
  <div class="ring"><svg width="12" height="16" viewBox="0 0 20 26"><path fill="#fff" d="M10 0a9 9 0 019 9c0 7-9 17-9 17S1 16 1 9a9 9 0 019-9z"/><circle cx="10" cy="9" r="3.5" fill="#000"/></svg></div>
  <div>123, Building Name, Street<br>City, State XY 123456</div>
</div>
<div class="abs foot-info" style="left:528px">
  <div class="ring"><svg width="15" height="15" viewBox="0 0 24 24"><path fill="#fff" d="M6.6 10.8a15 15 0 006.6 6.6l2.2-2.2c.3-.3.7-.4 1-.2 1.1.4 2.3.6 3.6.6.6 0 1 .4 1 1V20c0 .6-.4 1-1 1A17 17 0 013 4c0-.6.4-1 1-1h3.5c.6 0 1 .4 1 1 0 1.3.2 2.5.6 3.6.1.3 0 .7-.2 1z"/></svg></div>
  <div>Phone<br>123-456-7890</div>
</div>
<div class="abs foot-info" style="left:765px">
  <div class="ring"><svg width="15" height="12" viewBox="0 0 24 18"><rect x="1" y="1" width="22" height="16" rx="2" fill="#fff"/><path d="M2 3l10 7 10-7" stroke="#000" stroke-width="2" fill="none"/></svg></div>
  <div>E-Mail<br>Info@fenwickgrading-example.net</div>
</div>

<div class="abs divider"></div>
<div class="abs copy">© 2024 Fenwick Grading LTD . All Rights Reserved.</div>
<div class="abs social" style="left:905px"></div>
<div class="abs social" style="left:945px"></div>
<div class="abs social" style="left:985px"></div>
<div class="abs social" style="left:1025px"></div>

</body>
</html>
```